Pellham Grove Trust - New Website Designed

I need a site that looks like this http://www.quorlandgiving.org for boat donations. So please replace the cars with boats.

```html
<!DOCTYPE html>
<html lang="en">
<head>
<meta charset="utf-8">
<title>Pellham Grove Trust</title>
<link href="https://fonts.googleapis.com/css2?family=Montserrat:wght@500;600;700&family=Open+Sans:wght@400;600;700&display=swap" rel="stylesheet">
<style>
:root{
  --blue:#1762b8;
  --blue-dark:#0e4d97;
  --navy:#0d3d82;
  --red:#c3132f;
  --red-dark:#a00c22;
  --grey-bg:#ececec;
  --text:#333;
  --footer:#2a2a2a;
  --white:#fff;
}
*{box-sizing:border-box;margin:0;padding:0}
html,body{width:1200px;height:2571px;overflow:hidden}
body{position:relative;font-family:"Open Sans",Arial,sans-serif;color:var(--text);background:var(--white)}
.abs{position:absolute}
.heading{font-family:"Montserrat",Arial,sans-serif;font-weight:700;color:var(--blue);letter-spacing:.3px}

/* header */
.topbar{left:0;top:0;width:1200px;height:94px;background:var(--blue)}
.brand{left:98px;top:28px;display:flex;align-items:center;gap:14px;color:var(--white);font-family:"Montserrat",Arial,sans-serif;font-weight:700;font-size:24px}
.brand-dot{width:30px;height:30px;border-radius:50%;background:var(--white)}
.navbar{left:0;top:94px;width:1200px;height:60px;background:var(--blue-dark)}
.nav{left:98px;top:94px;height:60px;display:flex;align-items:center;list-style:none}
.nav li{color:var(--white);font-size:16px;font-weight:600;margin-right:52px}
.hero{left:0;top:154px;width:1200px;height:515px;background:linear-gradient(180deg,#2f78c9 0%,#6a9ccc 45%,#e69a58 68%,#233754 78%,#1b2a40 100%)}

/* donate panel */
.donate{left:747px;top:65px;width:353px;height:569px;background:var(--red)}
.donate-call{left:0;top:0;width:353px;height:80px;background:var(--red-dark);color:var(--white);text-align:center;font-family:"Montserrat",Arial,sans-serif;font-weight:700}
.donate-call p{font-size:19px;margin-top:-6px}
.donate-call .num{font-size:19px;margin-top:14px}
.donate-chevron{left:0;top:70px}
.donate-title{left:0;top:122px;width:353px;text-align:center;color:var(--white);font-family:"Montserrat",Arial,sans-serif;font-weight:700;font-size:19px}
.field{position:absolute;height:40px;background:var(--white);border-radius:3px;font-size:13px;color:#555;padding:0 10px;display:flex;align-items:center;justify-content:space-between}
.field.select::after{content:"";border:5px solid transparent;border-top:6px solid #333;margin-top:5px}
.donate-btn{left:18px;top:494px;width:317px;height:42px;background:var(--navy);border:1px solid var(--white);color:var(--white);font-size:15px;font-weight:600;display:flex;align-items:center;justify-content:center}

/* how */
.how-title{left:0;top:745px;width:1200px;text-align:center;font-size:28px}
.how-text{left:180px;top:796px;width:840px;text-align:center;font-size:13.5px;line-height:22px}
.step{position:absolute;top:883px;width:300px;height:100px}
.step-icon{position:absolute;left:0;top:10px;width:76px;height:76px;border-radius:50%;display:flex;align-items:center;justify-content:center}
.step-num{position:absolute;left:40px;top:0;width:28px;height:28px;border-radius:50%;border:2px solid var(--white);color:var(--white);font-size:14px;font-weight:700;display:flex;align-items:center;justify-content:center}
.step h3{position:absolute;left:95px;top:0;font-family:"Montserrat",Arial,sans-serif;font-size:19px;font-weight:600;color:var(--blue)}
.step p{position:absolute;left:95px;top:32px;width:200px;font-size:12.5px;line-height:19px}
.step-sep{position:absolute;top:890px;width:1px;height:92px;background:#ccc}

/* why */
.why{left:0;top:1071px;width:1200px;height:497px;background:var(--grey-bg)}
.why-title{left:98px;top:1140px;font-size:26px}
.why-rule{left:98px;top:1189px;width:170px;height:2px;background:var(--blue)}
.why-list{left:98px;top:1222px;list-style:none}
.why-list li{display:flex;align-items:center;gap:14px;height:36px;font-size:14px}
.why-photo{left:531px;top:1100px;width:669px;height:468px;background:linear-gradient(135deg,#d9d9d9 0%,#7d8a9c 40%,#3c4a66 70%,#c9c2b6 100%)}

/* faq */
.faq-title{left:0;top:1650px;width:1200px;text-align:center;font-size:27px}
.faq-rule{left:538px;top:1706px;width:124px;height:2px;background:var(--blue)}
.boat-photo{left:60px;top:1851px;width:489px;height:180px;border-radius:40% 20% 50% 50%/40% 30% 60% 60%;background:linear-gradient(180deg,#f2f2f2 0%,#cfd3d8 55%,#6d747c 100%)}
.acc{position:absolute;left:597px;width:447px;height:46px;border-radius:23px;display:flex;align-items:center;font-size:15.5px;font-weight:600}
.acc-sign{width:40px;height:40px;border-radius:50%;margin:0 18px 0 2px;display:flex;align-items:center;justify-content:center;color:var(--white);font-size:24px;font-weight:700}
.acc.open{background:var(--red);color:var(--white);width:446px}
.acc.open .acc-sign{background:var(--white);color:var(--red)}
.acc.closed{border:2px solid var(--blue);color:var(--navy)}
.acc.closed .acc-sign{background:var(--navy)}
.faq-answer{left:597px;top:1858px;width:503px;font-size:12.5px;line-height:20px;text-align:justify}

/* footer */
.footer{left:0;top:2150px;width:1200px;height:421px;background:var(--footer);color:var(--white)}
.foot-brand{left:98px;top:2282px;width:230px;display:flex;flex-direction:column;align-items:center;gap:14px;font-family:"Montserrat",Arial,sans-serif;font-weight:700;font-size:17px;color:var(--white);white-space:nowrap}
.foot-brand span.dot{width:40px;height:40px;border-radius:50%;background:var(--white)}
.foot-h{font-family:"Montserrat",Arial,sans-serif;font-weight:600;font-size:17px;color:var(--white)}
.foot-h::after{content:"";display:block;width:104px;height:2px;background:var(--white);margin-top:10px}
.links{left:384px;top:2264px;list-style:none;color:var(--white)}
.links li{font-size:14px;height:31.5px}
.links li::before{content:"›";margin-right:8px}
.contact-item{position:absolute;left:560px;display:flex;gap:16px;color:var(--white)}
.c-ico{width:38px;height:38px;border-radius:50%;border:1.5px solid var(--white);display:flex;align-items:center;justify-content:center;flex:none}
.contact-item b{display:block;font-size:14px;font-weight:700}
.contact-item span{font-size:13px;line-height:20px}
.ff{position:absolute;border:1px solid #bbb;border-radius:3px;font-size:11.5px;padding:6px 10px;color:var(--white)}
.send{left:812px;top:2386px;width:120px;height:38px;background:var(--white);color:var(--navy);font-size:13px;font-weight:700;display:flex;align-items:center;justify-content:center;border-radius:2px}
.foot-rule{left:98px;top:2494px;width:1004px;height:1px;background:#888}
.copy{left:98px;top:2522px;font-size:13px;font-weight:600;color:var(--white)}
.social{left:948px;top:2516px;display:flex;gap:9px}
.social span{width:32px;height:32px;border-radius:50%;border:1.5px solid var(--white)}
</style>
</head>
<body>

<header>
  <div class="abs topbar"></div>
  <div class="abs brand"><span class="brand-dot"></span>PELLHAM GROVE TRUST</div>
  <div class="abs navbar"></div>
  <ul class="abs nav">
    <li>HOME</li><li>HOW TO DONATE</li><li>WHY DONATE</li><li>FAQ</li><li>CONTACT</li>
  </ul>
</header>

<div class="abs hero" role="img" aria-label="Smiling soldier in camouflage beside a wooden boat silhouetted against a sunset sea"></div>

<form class="abs donate">
  <div class="abs donate-call"><p>CALL TODAY TO DONATE</p><p class="num">1-800-555-0148</p></div>
  <svg class="abs donate-chevron" width="353" height="24" viewBox="0 0 353 24"><polygon points="0,0 353,0 353,6 176,22 0,6" fill="var(--red-dark)"/><polyline points="0,6 176,22 353,6" fill="none" stroke="#fff" stroke-width="1.5"/></svg>
  <div class="abs donate-title">DONATE YOUR BOAT ONLINE</div>
  <div class="field" style="left:18px;top:177px;width:151px">Name</div>
  <div class="field" style="left:185px;top:177px;width:151px">Email</div>
  <div class="field" style="left:18px;top:228px;width:151px">Phone Number</div>
  <div class="field" style="left:185px;top:228px;width:151px">Cell Phone</div>
  <div class="field" style="left:18px;top:280px;width:318px">City</div>
  <div class="field select" style="left:18px;top:331px;width:151px">State</div>
  <div class="field" style="left:185px;top:331px;width:151px">Zip Code</div>
  <div class="field select" style="left:18px;top:382px;width:151px">Choose Year</div>
  <div class="field select" style="left:185px;top:382px;width:151px">Choose Make</div>
  <div class="field" style="left:18px;top:434px;width:318px">Boat Model</div>
  <div class="abs donate-btn">DONATE NOW</div>
</form>

<section>
  <h2 class="abs heading how-title">HOW TO DONATE</h2>
  <p class="abs how-text">Nemo enim ipsam voluptatem quia voluptas sit aspernatur aut odit aut fugit, sed quia consequuntur magni dolores eos qui ratione voluptatem sequi nesciunt.</p>

  <div class="step" style="left:98px">
    <div class="step-icon" style="background:var(--blue)"><svg width="34" height="34" viewBox="0 0 24 24" fill="none" stroke="#fff" stroke-width="1.8"><path d="M5 3h4l2 5-2.5 1.5a11 11 0 0 0 6 6L16 13l5 2v4a2 2 0 0 1-2 2A16 16 0 0 1 3 5a2 2 0 0 1 2-2z"/></svg></div>
    <div class="step-num" style="background:var(--red)">1</div>
    <h3>Call Us Now</h3>
    <p>Nam libero tempore, cum soluta nobis est eligendi optio cumque nihil impedit quon.</p>
  </div>
  <div class="step-sep" style="left:417px"></div>
  <div class="step" style="left:455px">
    <div class="step-icon" style="background:var(--red)"><svg width="34" height="34" viewBox="0 0 24 24" fill="none" stroke="#fff" stroke-width="2"><path d="M12 2v10"/><path d="M12 12a5 5 0 1 1-5 5"/><path d="M8 5h8"/></svg></div>
    <div class="step-num" style="background:var(--blue)">2</div>
    <h3>We Tow It</h3>
    <p>Nam libero tempore, cum soluta nobis est eligendi optio cumque nihil impedit quon.</p>
  </div>
  <div class="step-sep" style="left:777px"></div>
  <div class="step" style="left:810px">
    <div class="step-icon" style="background:var(--blue)"><svg width="32" height="32" viewBox="0 0 24 24" fill="none" stroke="#fff" stroke-width="2"><path d="M4 20l1-5L16 4l4 4L9 19z"/><path d="M3 22h18"/></svg></div>
    <div class="step-num" style="background:var(--red)">3</div>
    <h3>Tax Write Off</h3>
    <p>Nam libero tempore, cum soluta nobis est eligendi optio cumque nihil impedit quon.</p>
  </div>
</section>

<section>
  <div class="abs why"></div>
  <div class="abs why-photo" role="img" aria-label="Navy service member shaking hands with a civilian across a desk with paperwork"></div>
  <h2 class="abs heading why-title">WHY DONATE YOUR BOAT TO US</h2>
  <div class="abs why-rule"></div>
  <ul class="abs why-list">
    <li><svg width="14" height="14" viewBox="0 0 14 14"><circle cx="7" cy="7" r="7" fill="var(--navy)"/><path d="M4 7h5M7 4l3 3-3 3" stroke="#fff" stroke-width="1.6" fill="none"/></svg>Nam libero tempore, cum soluta nobis est eligendi optio cumque.</li>
    <li><svg width="14" height="14" viewBox="0 0 14 14"><circle cx="7" cy="7" r="7" fill="var(--navy)"/><path d="M4 7h5M7 4l3 3-3 3" stroke="#fff" stroke-width="1.6" fill="none"/></svg>Pedit quo minus id quod maxime placeat facere possimus.</li>
    <li><svg width="14" height="14" viewBox="0 0 14 14"><circle cx="7" cy="7" r="7" fill="var(--navy)"/><path d="M4 7h5M7 4l3 3-3 3" stroke="#fff" stroke-width="1.6" fill="none"/></svg>Vero eos et accusamus et iusto odio dignissimos ducimus quin.</li>
    <li><svg width="14" height="14" viewBox="0 0 14 14"><circle cx="7" cy="7" r="7" fill="var(--navy)"/><path d="M4 7h5M7 4l3 3-3 3" stroke="#fff" stroke-width="1.6" fill="none"/></svg>Harum quidem rerum facilis est et expedita distinctio.</li>
    <li><svg width="14" height="14" viewBox="0 0 14 14"><circle cx="7" cy="7" r="7" fill="var(--navy)"/><path d="M4 7h5M7 4l3 3-3 3" stroke="#fff" stroke-width="1.6" fill="none"/></svg>Necessitatibus saepe eveniet ut et voluptates repudiandae.</li>
    <li><svg width="14" height="14" viewBox="0 0 14 14"><circle cx="7" cy="7" r="7" fill="var(--navy)"/><path d="M4 7h5M7 4l3 3-3 3" stroke="#fff" stroke-width="1.6" fill="none"/></svg>Aut reiciendis voluptatibus maiores alias consequatur.</li>
    <li><svg width="14" height="14" viewBox="0 0 14 14"><circle cx="7" cy="7" r="7" fill="var(--navy)"/><path d="M4 7h5M7 4l3 3-3 3" stroke="#fff" stroke-width="1.6" fill="none"/></svg>Similique sunt in culpa qui officia deserunt mollitia.</li>
    <li><svg width="14" height="14" viewBox="0 0 14 14"><circle cx="7" cy="7" r="7" fill="var(--navy)"/><path d="M4 7h5M7 4l3 3-3 3" stroke="#fff" stroke-width="1.6" fill="none"/></svg>Perferendis doloribus asperiores repellat.</li>
  </ul>
</section>

<section>
  <h2 class="abs heading faq-title">FREQUENTLY ASKED QUESTIONS</h2>
  <div class="abs faq-rule"></div>
  <div class="abs boat-photo" role="img" aria-label="White motor yacht shown from the side"></div>
  <div class="acc open" style="top:1784px"><span class="acc-sign">−</span>Nemo enim ipsam voluptatem quia voluptas?</div>
  <p class="abs faq-answer">Sed ut perspiciatis unde omnis iste natus error sit voluptatem accusantium doloremque laudantium, totam rem aperiam, eaque ipsa quae ab illo inventore veri tatis et quasi architectos.</p>
  <div class="acc closed" style="top:1950px"><span class="acc-sign">+</span>Sed quia non numquam eius modi tempora?</div>
  <div class="acc closed" style="top:2014px"><span class="acc-sign">+</span>Ut enim ad minima veniam, quis nostrum?</div>
</section>

<footer>
  <div class="abs footer"></div>
  <div class="abs foot-brand"><span class="dot"></span>PELLHAM GROVE TRUST</div>

  <h4 class="abs foot-h" style="left:384px;top:2208px">QUICK LINKS</h4>
  <ul class="abs links">
    <li>Home</li><li>About</li><li>How To Donate</li><li>Why Donate</li><li>FAQ</li><li>Contact Us</li>
  </ul>

  <h4 class="abs foot-h" style="left:560px;top:2208px">CONTACT US</h4>
  <div class="contact-item" style="top:2266px">
    <div class="c-ico"><svg width="14" height="16" viewBox="0 0 14 18"><path d="M7 0a7 7 0 0 0-7 7c0 5 7 11 7 11s7-6 7-11a7 7 0 0 0-7-7z" fill="#fff"/><circle cx="7" cy="7" r="2.5" fill="var(--footer)"/></svg></div>
    <div><b>ADDRESS,</b><span>Larkmoor Road, Eastvale,<br>6150.</span></div>
  </div>
  <div class="contact-item" style="top:2336px">
    <div class="c-ico"><svg width="10" height="16" viewBox="0 0 10 16"><rect x="1" y="1" width="8" height="14" rx="1.5" fill="none" stroke="#fff" stroke-width="1.6"/></svg></div>
    <div><b>PHONE:</b><span>1-800-555-0148</span></div>
  </div>
  <div class="contact-item" style="top:2401px">
    <div class="c-ico"><svg width="15" height="11" viewBox="0 0 15 11"><rect width="15" height="11" rx="1" fill="#fff"/><path d="M0 1l7.5 5L15 1" stroke="var(--footer)" stroke-width="1.4" fill="none"/></svg></div>
    <div><b>Mail:</b><span>info@pellhamgrove.org</span></div>
  </div>

  <h4 class="abs foot-h" style="left:812px;top:2208px">CONTACT FORM</h4>
  <div class="ff" style="left:812px;top:2261px;width:140px;height:36px">Name</div>
  <div class="ff" style="left:960px;top:2261px;width:140px;height:36px">Phone</div>
  <div class="ff" style="left:812px;top:2305px;width:288px;height:68px">Message</div>
  <div class="abs send">SEND MESSAGE</div>

  <div class="abs foot-rule"></div>
  <p class="abs copy">Copyright © 2017 Pellham Grove Trust. All Right Reserved</p>
  <div class="abs social" aria-label="Social links"><span></span><span></span><span></span><span></span></div>
</footer>

</body>
</html>
```